Tandem Hearth Works Pty Ltd

We need business cards for a company based in Perth, we install, service and maintain fire equipment.
On the front we want a great design with our logo and a small spot for our full company name, general company email address and office number. On the back we need space for our name, title, mobile number and email address on the back.

Target Market(s)

Facility managers and commercial/industrial building owners/occupiers.

Contact Information for Business Card

Font styles to use
Sans Serif

Requirements
Must have
• Please only submit 5 of your best samples.
Darker tones are preferred.
Nice to have
• We want to use, black, red and grey. Keep it modern and clean.
I've attached the company logo and a sample of a boarder we use on our emergency plans.
Should not have
• No preference. Let the designer choose.

```html
<!DOCTYPE html>
<html lang="en">
<head>
<meta charset="utf-8">
<title>Tandem Hearth Works – Business Cards</title>
<link rel="stylesheet" href="https://fonts.googleapis.com/css2?family=Oswald:wght@500;600&family=Poppins:wght@400;600;700&display=swap">
<style>
  :root {
    --backdrop: #141414;
    --card-black: #0b0b0b;
    --card-white: #ffffff;
    --brand-red: #e3212b;
    --text-grey: #cfcfcf;
    --text-dark: #1a1a1a;
  }
  * { margin: 0; padding: 0; box-sizing: border-box; }
  html, body {
    width: 1200px; height: 900px; overflow: hidden;
    background: radial-gradient(circle at 50% 40%, #2a2a2a 0%, var(--backdrop) 75%);
    font-family: "Poppins", sans-serif;
  }
  .card {
    position: absolute;
    border-radius: 26px;
    box-shadow: 0 18px 40px rgba(0,0,0,0.55);
    overflow: hidden;
  }

  /* Front card */
  .card-front {
    left: 60px; top: 250px; width: 520px; height: 298px;
    background: var(--card-black);
  }
  .front-brand {
    position: absolute; left: 40px; top: 34px;
    display: flex; align-items: flex-start; gap: 12px;
  }
  .brand-square {
    width: 14px; height: 14px; background: var(--brand-red); flex: none;
    margin-top: 10px;
  }
  .front-brand-name {
    font-family: "Poppins", sans-serif; font-weight: 700;
    font-size: 44px; line-height: 1.05; letter-spacing: -0.5px;
    color: var(--brand-red);
  }
  .name-band {
    position: absolute; left: 40px; right: 0; top: 140px; height: 22px;
    background: var(--brand-red);
    display: flex; align-items: center; padding-left: 8px;
  }
  .name-band span {
    font-family: "Poppins", sans-serif; font-weight: 600;
    font-size: 13px; letter-spacing: 0.6px; text-transform: uppercase;
    color: var(--card-black);
  }
  .front-contacts {
    position: absolute; left: 250px; top: 192px;
    color: var(--text-grey); font-size: 14px; letter-spacing: 0.4px;
  }

  /* Back card */
  .card-back {
    left: 620px; top: 250px; width: 520px; height: 298px;
    background: var(--card-white);
  }
  .holder-name {
    position: absolute; left: 36px; top: 28px;
    font-family: "Oswald", sans-serif; font-weight: 600;
    font-size: 22px; letter-spacing: 0.5px; color: var(--text-dark);
  }
  .holder-title {
    position: absolute; left: 36px; top: 58px;
    font-family: "Oswald", sans-serif; font-weight: 500;
    font-size: 12px; letter-spacing: 0.5px; color: var(--brand-red);
  }
  .title-rule {
    position: absolute; left: 36px; top: 86px;
    width: 34px; height: 2px; background: var(--brand-red);
  }
  .back-contacts {
    position: absolute; left: 36px; top: 130px;
    color: var(--text-dark); font-size: 13px; letter-spacing: 0.3px;
  }
  .back-brand {
    position: absolute; right: 36px; top: 192px;
    display: flex; align-items: flex-start; gap: 10px;
  }
  .back-brand .brand-square { width: 12px; height: 12px; margin-top: 9px; }
  .back-brand-name {
    font-family: "Poppins", sans-serif; font-weight: 700;
    font-size: 32px; line-height: 1.05; letter-spacing: -0.5px;
    color: var(--brand-red);
  }

  .contact-row { display: flex; align-items: center; gap: 10px; margin-bottom: 8px; }
  .contact-row svg { width: 12px; height: 12px; flex: none; }
</style>
</head>
<body>

  <section class="card card-front" aria-label="Business card front">
    <div class="front-brand">
      <div class="brand-square"></div>
      <div class="front-brand-name">Tandem<br>Hearth Works</div>
    </div>
    <div class="name-band"><span>Tandem Hearth Works Pty Ltd</span></div>
    <div class="front-contacts">
      <div class="contact-row">
        <svg viewBox="0 0 24 24" aria-hidden="true"><path fill="#e3212b" d="M6.6 10.8a15.1 15.1 0 0 0 6.6 6.6l2.2-2.2c.3-.3.7-.4 1-.2 1.1.4 2.3.6 3.6.6.6 0 1 .4 1 1V20c0 .6-.4 1-1 1A17 17 0 0 1 3 4c0-.6.4-1 1-1h3.5c.6 0 1 .4 1 1 0 1.3.2 2.5.6 3.6.1.3 0 .7-.2 1z"/></svg>
        <span>000 000 0000</span>
      </div>
      <div class="contact-row">
        <svg viewBox="0 0 24 24" aria-hidden="true"><path fill="#e3212b" d="M2 5h20v14H2z"/><path fill="none" stroke="#0b0b0b" stroke-width="2" d="M2 5l10 8 10-8"/></svg>
        <span>office@tandemhearth.com.au</span>
      </div>
    </div>
  </section>

  <section class="card card-back" aria-label="Business card back">
    <div class="holder-name">YOUR NAME</div>
    <div class="holder-title">JOB TITLE</div>
    <div class="title-rule"></div>
    <div class="back-contacts">
      <div class="contact-row">
        <svg viewBox="0 0 24 24" aria-hidden="true"><path fill="#e3212b" d="M6.6 10.8a15.1 15.1 0 0 0 6.6 6.6l2.2-2.2c.3-.3.7-.4 1-.2 1.1.4 2.3.6 3.6.6.6 0 1 .4 1 1V20c0 .6-.4 1-1 1A17 17 0 0 1 3 4c0-.6.4-1 1-1h3.5c.6 0 1 .4 1 1 0 1.3.2 2.5.6 3.6.1.3 0 .7-.2 1z"/></svg>
        <span>000 000 0000</span>
      </div>
      <div class="contact-row">
        <svg viewBox="0 0 24 24" aria-hidden="true"><path fill="#e3212b" d="M2 5h20v14H2z"/><path fill="none" stroke="#ffffff" stroke-width="2" d="M2 5l10 8 10-8"/></svg>
        <span>name@tandemhearth.com.au</span>
      </div>
    </div>
    <div class="back-brand">
      <div class="brand-square"></div>
      <div class="back-brand-name">Tandem<br>Hearth Works</div>
    </div>
  </section>

</body>
</html>
```